Marta's Dwellings website

We need a simple website for our property investment business in the UK. We basically need our contact details and brief description.We have the company logo already done (via ArtFlockly) so please use these:https://drive.google.com/drive/folders/1szJ3iRhelElZ40NIFT7w-c14MaY3Y_oV?usp=sharingYou could use some stock photos of UK houses for now.Let me know when to provide more detailed descriptions, etc

Coding

Coded - Design and coding required

Number of Pages Required

1 page

Colors

Designer to choose colors to be used in the design.

```html
<!DOCTYPE html>
<html lang="en">
<head>
<meta charset="utf-8">
<title>Marta's Dwellings</title>
<link href="https://fonts.googleapis.com/css2?family=Raleway:wght@400;500&family=Open+Sans:wght@400;600&display=swap" rel="stylesheet">
<style>
:root{
  --ink:#1b1b1b;
  --dark:#333333;
  --header:#2e2f31;
  --footer:#1c1c1c;
  --strip:rgba(52,52,52,.93);
  --muted:#555555;
  --rule:#a9a9a9;
  --card:#e9e9e9;
  --white:#ffffff;
  --head-font:'Raleway',sans-serif;
  --body-font:'Open Sans',sans-serif;
}
*{margin:0;padding:0;box-sizing:border-box}
html,body{width:1200px;height:2594px;overflow:hidden}
body{position:relative;background:var(--white);font-family:var(--body-font);color:var(--muted)}
.abs{position:absolute}

/* header */
.site-header{left:0;top:0;width:1200px;height:112px;background:var(--header)}
.brand{left:143px;top:36px;display:flex;align-items:center;gap:12px;color:var(--white);font-family:var(--head-font);font-size:19px;letter-spacing:3px;text-transform:uppercase}
.brand-mark{width:26px;height:26px;background:var(--white)}
.header-phone{right:145px;top:22px;color:var(--white);font-family:var(--head-font);font-size:20px;display:flex;align-items:center;gap:8px}
.main-nav{right:145px;top:66px;display:flex;gap:45px}
.main-nav a{color:var(--white);font-family:var(--head-font);font-size:15.5px;text-decoration:none;text-transform:uppercase}
.main-nav a.active{text-decoration:underline;text-underline-offset:4px}

/* hero */
.hero{left:0;top:112px;width:1200px;height:502px;background:linear-gradient(180deg,#b9c6d4 0%,#9a5a3a 35%,#b4552e 65%,#8a7a5e 100%)}
.hero-arrow{top:350px;width:28px;height:28px;background:var(--ink);display:flex;align-items:center;justify-content:center}

/* headings */
.section-title{left:0;width:1200px;text-align:center;font-family:var(--head-font);font-weight:400;font-size:32px;text-transform:uppercase;color:var(--ink)}
.section-title.light{color:var(--white)}
.title-rule{left:546px;width:108px;height:3px;background:var(--rule)}

/* welcome */
.welcome-text{left:144px;top:762px;width:912px;text-align:center;font-size:13.4px;line-height:25.6px;color:var(--muted)}
.read-more{left:548px;top:902px;width:104px;height:40px;background:#000;color:var(--white);font-family:var(--head-font);font-size:14px;display:flex;align-items:center;justify-content:center}

/* services */
.services{left:0;top:1022px;width:1200px;height:688px;background:var(--dark)}
.services-photo{left:144px;top:1175px;width:456px;height:456px;background:linear-gradient(135deg,#5b5e62,#3c3e40 60%,#8a8c8e)}
.services-panel{left:600px;top:1175px;width:456px;height:456px;background:var(--white)}
.service{left:640px;display:flex;gap:16px}
.service svg{flex:none}
.service h3{font-family:var(--head-font);font-weight:400;font-size:18px;color:var(--ink);margin:0 0 6px}
.service p{font-size:10.6px;line-height:17px;color:var(--muted);width:292px}

/* news */
.news-card{top:1875px;width:265px;height:144px;background:var(--card)}
.news-date{top:1891px;width:48px;height:62px;background:#000;color:var(--white);text-align:center;font-family:var(--head-font)}
.news-date b{display:block;font-weight:400;font-size:31px;line-height:36px;margin-top:2px}
.news-date span{font-size:13px}
.news-body{top:1886px;width:215px}
.news-body h3{font-family:var(--head-font);font-weight:400;font-size:15.5px;line-height:21px;color:var(--ink);margin-bottom:6px}
.news-body p{font-size:10.6px;line-height:18px;color:var(--muted)}

/* map + contact */
.map{left:0;top:2100px;width:1200px;height:398px;background:linear-gradient(160deg,#eceff1,#e2e5e7 50%,#eef0f0)}
.contact-strip{left:0;top:2388px;width:1200px;height:110px;background:var(--strip);color:var(--white);font-size:16.5px}
.contact-line{display:flex;align-items:center;gap:7px}

/* footer */
.site-footer{left:0;top:2498px;width:1200px;height:96px;background:var(--footer)}
.footer-links{left:144px;top:2526px;font-size:10.5px;color:#cfcfcf;display:flex;gap:8px}
.footer-links a{color:#cfcfcf;text-decoration:none}
.copyright{left:144px;top:2552px;font-size:10.5px;color:#bdbdbd}
.social{top:2518px;width:32px;height:32px;border:1px solid #4d4d4d}
</style>
</head>
<body>

<header class="abs site-header">
  <div class="abs brand"><span class="brand-mark"></span>Marta's Dwellings</div>
  <div class="abs header-phone">
    <svg width="16" height="16" viewBox="0 0 24 24"><path fill="#fff" d="M6.6 10.8a15 15 0 0 0 6.6 6.6l2.2-2.2c.3-.3.7-.4 1-.2 1.1.4 2.3.6 3.6.6.6 0 1 .4 1 1V20c0 .6-.4 1-1 1A17 17 0 0 1 3 4c0-.6.4-1 1-1h3.5c.6 0 1 .4 1 1 0 1.3.2 2.5.6 3.6.1.3 0 .7-.2 1z"/></svg>
    470 218 9034
  </div>
  <nav class="abs main-nav">
    <a class="active" href="#">Home</a><a href="#">About us</a><a href="#">Services</a><a href="#">News</a><a href="#">Contact us</a>
  </nav>
</header>

<div class="abs hero" role="img" aria-label="Photo of a red brick English house with white windows and a lamp post"></div>
<div class="abs hero-arrow" style="left:0"><svg width="14" height="14" viewBox="0 0 14 14"><path d="M12 7H3M7 2.5 2.5 7 7 11.5" stroke="#fff" stroke-width="2.2" fill="none"/></svg></div>
<div class="abs hero-arrow" style="right:0"><svg width="14" height="14" viewBox="0 0 14 14"><path d="M2 7h9M7 2.5 11.5 7 7 11.5" stroke="#fff" stroke-width="2.2" fill="none"/></svg></div>

<h1 class="abs section-title" style="top:688px">Welcome to Marta's Dwellings</h1>
<div class="abs title-rule" style="top:744px"></div>
<p class="abs welcome-text">Aenean sed quam non sapien faucibus consequat vitae sit amet orci. Praesent quis risus mi. In mollis nulla in pulvinar dictum. Vivamus interdum sagittis felis, ut dapibus ligula feugiat ac. In dictum sapien eu tellus finibus fermentum. Aenean faucibus lacus ut mollis commodo. Donec vestibulum odio sem, ac laoreet massa ullamcorper id. Donec molestie nisi et tellus hendrerit vehicula. Nunc eu ligula sed quam pulvinar maximus in vitae eros. Proin porta fermentum ipsum, vel porttitor turpis venenatis luctus. Vivamus volutpat eu sapien quis tempus. Aenean feugiat viverra lorem ac sagittis. Donec sit amet lectus nec mi tempor laoreet ac nec nunc. Duis id auctor sapien.</p>
<div class="abs read-more">Read More</div>

<section class="abs services"></section>
<h2 class="abs section-title light" style="top:1096px">Our Services</h2>
<div class="abs title-rule" style="top:1151px"></div>
<div class="abs services-photo" role="img" aria-label="Photo of model houses beside a calculator and phone on a wooden desk"></div>
<div class="abs services-panel"></div>

<div class="abs service" style="top:1226px">
  <svg width="68" height="68" viewBox="0 0 68 68" fill="none" stroke="#333" stroke-width="2"><rect x="22" y="4" width="34" height="44" rx="2"/><circle cx="39" cy="24" r="8"/><rect x="2" y="40" width="12" height="24"/><path d="M14 46h16l10 6h22v8H14"/></svg>
  <div><h3>Aliquam erat volutpat</h3><p>Etiam mattis augue vehicula odio posuere, sit amet tempus lectus luctus. Nulla facilisi. Etiam vel massa elementum, bibendum tellus venenatis, feugiat massa.</p></div>
</div>
<div class="abs service" style="top:1364px">
  <svg width="68" height="68" viewBox="0 0 68 68" fill="none" stroke="#333" stroke-width="2"><path d="M4 32 34 8l30 24"/><path d="M10 28v34h48V28"/><circle cx="34" cy="26" r="3"/><rect x="18" y="40" width="10" height="12"/><rect x="40" y="40" width="10" height="22"/><path d="M4 62h60"/></svg>
  <div><h3>Curabitur venenatis lacinia</h3><p>Etiam mattis augue vehicula odio posuere, sit amet tempus lectus luctus. Nulla facilisi. Etiam vel massa elementum, bibendum tellus venenatis, feugiat massa.</p></div>
</div>
<div class="abs service" style="top:1502px">
  <svg width="68" height="68" viewBox="0 0 68 68" fill="none" stroke="#333" stroke-width="2"><rect x="12" y="4" width="26" height="60"/><rect x="38" y="28" width="22" height="36"/><path d="M18 12h6M28 12h4M18 22h6M28 22h4M18 32h6M28 32h4M18 42h6M28 42h4M44 36h4M52 36h4M44 46h4M52 46h4M44 56h4M52 56h4M2 64h64"/></svg>
  <div><h3>Cras augue magna placerat</h3><p>Etiam mattis augue vehicula odio posuere, sit amet tempus lectus luctus. Nulla facilisi. Etiam vel massa elementum, bibendum tellus venenatis, feugiat massa.</p></div>
</div>

<h2 class="abs section-title" style="top:1784px">Latest News</h2>
<div class="abs title-rule" style="top:1840px"></div>

<div class="abs news-card" style="left:168px"></div>
<div class="abs news-date" style="left:144px"><b>13</b><span>MAY</span></div>
<div class="abs news-body" style="left:205px"><h3>Donec sit amet lectus nec mi tempor laoreet ac.</h3><p>Nullam accumsan purus vel tempus viverra. Mauris suscipit felis id nunc elementum varius. Praesent elementum nulla sit amet justo pellentesque scelerisque.</p></div>

<div class="abs news-card" style="left:479px"></div>
<div class="abs news-date" style="left:455px"><b>13</b><span>MAY</span></div>
<div class="abs news-body" style="left:516px"><h3>Donec sit amet lectus nec mi tempor laoreet ac.</h3><p>Nullam accumsan purus vel tempus viverra. Mauris suscipit felis id nunc elementum varius. Praesent elementum nulla sit amet justo pellentesque scelerisque.</p></div>

<div class="abs news-card" style="left:790px"></div>
<div class="abs news-date" style="left:766px"><b>13</b><span>MAY</span></div>
<div class="abs news-body" style="left:827px"><h3>Donec sit amet lectus nec mi tempor laoreet ac.</h3><p>Nullam accumsan purus vel tempus viverra. Mauris suscipit felis id nunc elementum varius. Praesent elementum nulla sit amet justo pellentesque scelerisque.</p></div>

<div class="abs map" role="img" aria-label="Street map showing the office location"></div>
<div class="abs contact-strip">
  <div class="abs contact-line" style="left:0;width:1200px;justify-content:center;top:14px">
    <svg width="10" height="15" viewBox="0 0 10 15"><path fill="#fff" d="M5 0a5 5 0 0 0-5 5c0 4 5 10 5 10s5-6 5-10a5 5 0 0 0-5-5zm0 7a2 2 0 1 1 0-4 2 2 0 0 1 0 4z"/></svg>
    Unit 7, Harrow Court, 14-16 Orchard Lane, Fenwick Ashby, Westshire, United Kingdom, WX4 9LT
  </div>
  <div class="abs contact-line" style="left:198px;top:54px">
    <svg width="14" height="14" viewBox="0 0 14 14"><circle cx="7" cy="4" r="3.5" fill="#fff"/><path fill="#fff" d="M0 14c0-4 3-6 7-6s7 2 7 6z"/></svg>
    Contact : Marta Louise Brennan
  </div>
  <div class="abs contact-line" style="left:512px;top:54px">
    <svg width="14" height="14" viewBox="0 0 24 24"><path fill="#fff" d="M6.6 10.8a15 15 0 0 0 6.6 6.6l2.2-2.2c.3-.3.7-.4 1-.2 1.1.4 2.3.6 3.6.6.6 0 1 .4 1 1V20c0 .6-.4 1-1 1A17 17 0 0 1 3 4c0-.6.4-1 1-1h3.5c.6 0 1 .4 1 1 0 1.3.2 2.5.6 3.6.1.3 0 .7-.2 1z"/></svg>
    Phone : 550 274 3816
  </div>
  <div class="abs contact-line" style="left:778px;top:54px">
    <svg width="16" height="12" viewBox="0 0 16 12"><rect width="16" height="12" fill="#fff"/><path d="M0 0l8 6 8-6" stroke="#343434" stroke-width="1.4" fill="none"/></svg>
    Email : hello@martasdwellings.example
  </div>
</div>

<footer class="abs site-footer"></footer>
<div class="abs footer-links"><a href="#">Home</a>|<a href="#">About us</a>|<a href="#">Services</a>|<a href="#">News</a>|<a href="#">Contact us</a></div>
<div class="abs copyright">Copyright © 2019 &nbsp;Marta's Dwellings. &nbsp;All rights reserved.</div>
<div class="abs social" style="left:943px"></div>
<div class="abs social" style="left:983px"></div>
<div class="abs social" style="left:1023px"></div>

</body>
</html>
```